Brand Identity Stationary Package

Hello I'm looking for a full branding package for my Property Management Company. I have a logo but looking to have the following
Business Card
Email signature
Facebook cover photo
Letterhead (word.doc)
#10 Envelope
Pocket Folder - link to 9x12 pocket folder design specs https://www.printorbit-example.ca/marketing-materials/presentation-folders
would like everything to match and be brand identifiable. The company looks after residential properties/apartments and some commercial properties. Attached is a zip of the files.
For Business Card
Name: Gareth Lindqvist
Position: Operations Manager
Number: 1 (555) 384-2917
Email: Gareth@harborkey-example.ca
Website: Harborkey-example.ca
Property Management

```html
<!DOCTYPE html>
<html lang="en">
<head>
<meta charset="utf-8">
<title>Harborkey Business Card</title>
<link rel="stylesheet" href="https://fonts.googleapis.com/css2?family=Roboto:wght@400;500;700&display=swap">
<style>
  :root {
    --bg: #1a1a1a;
    --card-white: #f7f7f7;
    --card-black: #0d0b0b;
    --brand-green: #7cc242;
    --ink-dark: #2a2a2a;
    --ink-grey: #5f5f5f;
    --rule: #3a3a3a;
    --ink-light: #e9e9e9;
  }
  * { margin: 0; padding: 0; box-sizing: border-box; }
  html, body {
    width: 1200px; height: 900px; overflow: hidden;
    background: var(--bg);
    font-family: "Roboto", sans-serif;
  }
  .stage {
    width: 1200px; height: 900px;
    display: flex; flex-direction: column;
    align-items: center; justify-content: center; gap: 40px;
  }
  .card {
    width: 700px; height: 400px; position: relative;
    border-radius: 4px; overflow: hidden;
    box-shadow: 0 12px 30px rgba(0,0,0,.55);
  }
  /* Front */
  .card-front {
    background: var(--card-white);
    border-bottom: 6px solid var(--brand-green);
    display: flex; align-items: center;
  }
  .front-brand {
    width: 340px; padding-left: 60px;
    display: flex; align-items: center;
  }
  .brand-name {
    font-weight: 700; font-size: 46px; letter-spacing: 1px;
    color: var(--ink-dark); text-transform: uppercase;
  }
  .divider {
    width: 2px; height: 190px; background: var(--rule);
    margin: 0 38px 0 0;
  }
  .contact { color: var(--ink-grey); font-size: 17px; line-height: 1.35; }
  .contact-name {
    color: var(--brand-green); font-weight: 500; font-size: 24px;
    text-transform: uppercase; letter-spacing: .5px;
  }
  .contact-role { font-size: 19px; margin-bottom: 14px; }
  .contact-address { margin-bottom: 6px; }
  .contact-line { display: flex; align-items: center; gap: 10px; }
  .contact-line svg { width: 16px; height: 16px; flex: none; }
  /* Back */
  .card-back {
    background: var(--card-black);
    display: flex; flex-direction: column;
    align-items: center; justify-content: center; gap: 70px;
  }
  .card-back .brand-name { color: var(--ink-light); font-size: 64px; letter-spacing: 2px; }
  .back-web { color: var(--ink-light); font-size: 20px; letter-spacing: 1px; }
  .back-web .accent { color: var(--brand-green); }
</style>
</head>
<body>
<main class="stage">
  <section class="card card-front">
    <div class="front-brand"><span class="brand-name">Harborkey</span></div>
    <div class="divider"></div>
    <div class="contact">
      <p class="contact-name">Gareth Lindqvist</p>
      <p class="contact-role">Operations Manager</p>
      <p class="contact-address">48 Alder Bay Crescent,<br>Richmond Hill, ON L4T 3K2</p>
      <p class="contact-line">
        <svg viewBox="0 0 24 24"><path fill="#7cc242" d="M6.6 10.8a15 15 0 0 0 6.6 6.6l2.2-2.2a1 1 0 0 1 1-.25 11.4 11.4 0 0 0 3.6.57 1 1 0 0 1 1 1V20a1 1 0 0 1-1 1A17 17 0 0 1 3 4a1 1 0 0 1 1-1h3.5a1 1 0 0 1 1 1c0 1.25.2 2.45.57 3.57a1 1 0 0 1-.25 1z"/></svg>
        1 (555) 384-2917
      </p>
      <p class="contact-line">
        <svg viewBox="0 0 24 24"><rect x="2" y="5" width="20" height="14" rx="1" fill="#7cc242"/><path d="M2.5 5.5 12 13l9.5-7.5" fill="none" stroke="#f7f7f7" stroke-width="1.6"/></svg>
        Gareth@harborkey-example.ca
      </p>
      <p class="contact-line">
        <svg viewBox="0 0 24 24" fill="none" stroke="#7cc242" stroke-width="1.8"><circle cx="12" cy="12" r="9.5"/><ellipse cx="12" cy="12" rx="4" ry="9.5"/><path d="M2.5 12h19"/></svg>
        www.harborkey-example.ca
      </p>
    </div>
  </section>

  <section class="card card-back">
    <span class="brand-name">Harborkey</span>
    <p class="back-web">www.<span class="accent">harborkey-example</span>.ca</p>
  </section>
</main>
</body>
</html>
```